BUSINESS CARD - HALLORAN FIELD SERVICES

I would like to create a business card for my fertilizer spreading business. I would like to incorporate my existing logo and also a description of the services offered. The business card will be given to farmers so must be kept simple but effective. It will also be left in stores so much also be eye catching in order to stand out from other cards.

Target Market(s)

FARMERS

Requirements
Must have
• FRONT OF CARD = EXISTING LOGO + "CUSTOMISED SPREADING" below the logo

REAR Of CARD = SERVICES OFFERED AND CONTACT DETAILS

- Bulk fertilizer including Lime, Gypsum, Manure & Compost
- Granular fertilizer including Single Super, Urea, Gran-am, & Custom Blends
- Modern equipment - Autosteer & Variable Rate Capable
- Friendly & Reliable Service
- Contact Gus: 0417 552 308
Nice to have
• utilize same color scheme as existing logo

```html
<!DOCTYPE html>
<html lang="en">
<head>
<meta charset="utf-8">
<title>Halloran Field Services – Business Card</title>
<link href="https://fonts.googleapis.com/css2?family=Lato:wght@400;700&display=swap" rel="stylesheet">
<style>
  :root {
    --orange: #f7931e;
    --orange-deep: #ec8412;
    --orange-soft: #f9a443;
    --charcoal: #4a4a4a;
    --ink: #333333;
    --white: #ffffff;
    --backdrop: #d4d4d4;
  }
  * { margin: 0; padding: 0; box-sizing: border-box; }
  html, body { width: 1200px; height: 900px; overflow: hidden; }
  body {
    background: var(--backdrop);
    font-family: "Lato", Arial, sans-serif;
    display: flex;
    align-items: center;
    justify-content: center;
    gap: 40px;
  }
  .card {
    position: relative;
    width: 540px;
    height: 330px;
    border-radius: 16px;
    overflow: hidden;
    box-shadow: 0 10px 24px rgba(0,0,0,0.25);
  }

  /* Rear: services & contact */
  .card-rear { background: var(--white); }
  .card-rear .wave { position: absolute; inset: 0; width: 100%; height: 100%; }
  .contact { position: absolute; left: 34px; top: 26px; }
  .contact-name { font-size: 20px; font-weight: 700; color: var(--ink); }
  .contact-title { font-size: 14px; color: var(--orange); margin-top: 2px; }
  .contact-phone {
    display: flex; align-items: center; gap: 6px;
    font-size: 15px; color: var(--ink); margin-top: 3px;
  }
  .contact-phone svg { width: 14px; height: 14px; }
  .services {
    position: absolute; left: 34px; top: 118px;
    list-style: none; font-size: 15px; line-height: 21px; color: var(--charcoal);
  }
  .services li { position: relative; padding-left: 18px; }
  .services li::before {
    content: ""; position: absolute; left: 0; top: 5px;
    width: 11px; height: 11px; border-radius: 50%; background: var(--orange);
  }

  /* Front: brand */
  .card-front { background: var(--orange); }
  .pattern-field {
    position: absolute; inset: 0;
    background: radial-gradient(circle at 30% 30%, var(--orange-soft), var(--orange) 55%, var(--orange-deep));
  }
  .brand {
    position: absolute; right: 30px; bottom: 22px;
    display: flex; align-items: center; gap: 14px;
    color: var(--white); font-weight: 700;
  }
  .brand-mark { width: 54px; height: 54px; border-radius: 50%; background: var(--white); flex: none; }
  .brand-name { font-size: 30px; line-height: 1; white-space: nowrap; }
  .brand-sub {
    font-size: 13px; letter-spacing: 5px; margin-top: 6px;
    border-top: 2px solid var(--white); border-bottom: 2px solid var(--white);
    padding: 2px 0; text-align: center;
  }
  .brand-tagline {
    font-size: 13px; letter-spacing: 2px; margin-top: 8px;
    text-align: center; white-space: nowrap;
  }
</style>
</head>
<body>

  <section class="card card-rear" aria-label="Card rear: services and contact">
    <svg class="wave" viewBox="0 0 540 330" preserveAspectRatio="none" aria-hidden="true">
      <path d="M0 220 C 60 235, 120 250, 200 275 C 300 305, 420 300, 540 330 L540 330 L0 330 Z" fill="var(--charcoal)"/>
      <path d="M0 232 C 60 248, 120 262, 200 288 C 300 318, 420 314, 540 340 L540 340 L0 340 Z" fill="var(--white)"/>
      <path d="M0 240 C 60 258, 130 274, 210 298 C 300 326, 400 326, 470 336 L0 336 Z" fill="var(--orange)"/>
    </svg>
    <div class="contact">
      <div class="contact-name">Gus</div>
      <div class="contact-title">ceo / General Manager</div>
      <div class="contact-phone">
        <svg viewBox="0 0 24 24" aria-hidden="true"><path fill="var(--orange)" d="M3 9c0-3 4-5 9-5s9 2 9 5v2h-5V9H8v2H3zM6 12h12l2 8H4z"/></svg>
        <span>0417 552 308</span>
      </div>
    </div>
    <ul class="services">
      <li>Bulk fertilizer including Lime, Gypsum, Manure &amp; Compost.</li>
      <li>Granular fertilizer including Single Super,</li>
      <li>Urea, Gran-am, &amp; Custom Blends.</li>
      <li>Modern equipment - Autosteer &amp; Variable Rate Capable.</li>
      <li>Friendly &amp; Reliable Service.</li>
    </ul>
  </section>

  <section class="card card-front" aria-label="Card front: brand">
    <div class="pattern-field" role="img" aria-label="Faint repeating brand pattern on orange"></div>
    <div class="brand">
      <div class="brand-mark"></div>
      <div>
        <div class="brand-name">Halloran Field</div>
        <div class="brand-sub">SERVICES</div>
        <div class="brand-tagline">CUSTOMISED SPREADING</div>
      </div>
    </div>
  </section>

</body>
</html>
```